Business Card Design

We are a manufacturing and distribution company with most of our customer base being supermarkets. We have established brand guidelines that are attached.

```html
<!DOCTYPE html>
<html lang="en">
<head>
<meta charset="utf-8">
<title>Veltaro Business Card</title>
<link href="https://fonts.googleapis.com/css2?family=Montserrat:wght@700;800&family=Arimo:wght@400&display=swap" rel="stylesheet">
<style>
  :root {
    --stage: #1f1f1f;
    --brand-blue: #0a68ad;
    --brand-red: #e1232b;
    --ink: #151515;
    --paper: #ffffff;
    --body-text: #1c1c1c;
  }
  * { box-sizing: border-box; margin: 0; padding: 0; }
  html, body {
    width: 1200px;
    height: 988px;
    overflow: hidden;
    background: var(--stage);
  }
  .stage {
    position: relative;
    width: 1200px;
    height: 988px;
  }
  .card {
    position: absolute;
    width: 700px;
    height: 400px;
    border-radius: 26px;
    overflow: hidden;
  }
  /* Back side */
  .card--back {
    left: 110px;
    top: 70px;
    background: var(--brand-blue);
    display: flex;
    align-items: center;
    justify-content: center;
    gap: 22px;
  }
  .card--back .brand-square {
    width: 46px;
    height: 46px;
    background: var(--paper);
  }
  .card--back .brand-name {
    font-family: "Montserrat", sans-serif;
    font-weight: 800;
    font-size: 68px;
    letter-spacing: 3px;
    color: var(--paper);
  }
  /* Front side */
  .card--front {
    left: 390px;
    top: 518px;
    background: var(--paper);
  }
  .front-mark {
    position: absolute;
    right: 56px;
    top: 56px;
    width: 190px;
    height: 190px;
    background: var(--brand-blue);
  }
  .front-info {
    position: absolute;
    left: 52px;
    top: 60px;
  }
  .front-info .brand-name {
    font-family: "Montserrat", sans-serif;
    font-weight: 800;
    font-size: 46px;
    letter-spacing: 2px;
    color: var(--ink);
    line-height: 1;
  }
  .person-name {
    margin-top: 22px;
    font-family: "Montserrat", sans-serif;
    font-weight: 800;
    font-size: 26px;
    letter-spacing: 1px;
    line-height: 1;
  }
  .person-name .first { color: var(--brand-red); }
  .person-name .last { color: var(--brand-blue); }
  .person-role,
  .address,
  .contact-list {
    font-family: "Arimo", Arial, sans-serif;
    font-size: 17px;
    color: var(--body-text);
  }
  .person-role { margin-top: 4px; }
  .address { margin-top: 20px; line-height: 1.3; font-style: normal; }
  .contact-list {
    list-style: none;
    margin-top: 18px;
    line-height: 1.55;
  }
  .contact-list li {
    display: flex;
    align-items: center;
    gap: 10px;
  }
  .contact-list svg {
    width: 15px;
    height: 15px;
    fill: var(--brand-blue);
    flex: none;
  }
</style>
</head>
<body>
<main class="stage">
  <section class="card card--back" aria-label="Card back">
    <span class="brand-square" aria-hidden="true"></span>
    <span class="brand-name">VELTARO</span>
  </section>

  <section class="card card--front" aria-label="Card front">
    <div class="front-info">
      <p class="brand-name">VELTARO</p>
      <p class="person-name"><span class="first">DANIEL</span> <span class="last">MORROW</span></p>
      <p class="person-role">CEO/Founder</p>
      <address class="address">2150 Kestrel Lane<br>Country Name, AB 40219</address>
      <ul class="contact-list">
        <li>
          <svg viewBox="0 0 24 24" aria-hidden="true"><path d="M6.6 10.8a15.1 15.1 0 0 0 6.6 6.6l2.2-2.2c.3-.3.7-.4 1-.2 1.1.4 2.3.6 3.6.6.6 0 1 .4 1 1V20c0 .6-.4 1-1 1A17 17 0 0 1 3 4c0-.6.4-1 1-1h3.5c.6 0 1 .4 1 1 0 1.3.2 2.5.6 3.6.1.3 0 .7-.2 1z"/></svg>
          555-014-2290
        </li>
        <li>
          <svg viewBox="0 0 24 24" aria-hidden="true"><path d="M2 5h20v14H2z M2 5l10 8 10-8" fill="none" stroke="#0a68ad" stroke-width="2.4"/></svg>
          hello@veltaro.com.au
        </li>
        <li>
          <svg viewBox="0 0 24 24" aria-hidden="true"><circle cx="12" cy="12" r="10"/><path d="M2 12h20M12 2c3 3 3 17 0 20M12 2c-3 3-3 17 0 20" fill="none" stroke="#fff" stroke-width="1.4"/></svg>
          www.veltaro.com.au
        </li>
      </ul>
    </div>
    <span class="front-mark" aria-hidden="true"></span>
  </section>
</main>
</body>
</html>
```